New Business Card Design Project

Use the flyer uploaded and website www.brightoakbuilders.com for inspiration.
List Our Services on Backside of business cards
Marcus Delling
Harborline Builders Inc.
Licensed General Contractors
858-471-6093

Contact Information for Business Card

Use the flyer uploaded and website www.brightoakbuilders.com for inspiration. List Our Services on Backside of business cards Marcus Delling Harborline Builders Inc. Licensed General Contractors 858-471-6093

```html
<!DOCTYPE html>
<html lang="en">
<head>
<meta charset="utf-8">
<title>Harborline Builders – Business Card</title>
<link href="https://fonts.googleapis.com/css2?family=Montserrat:wght@400;500;700&display=swap" rel="stylesheet">
<style>
  :root {
    --backdrop: #e9e6e1;
    --card: #232323;
    --ink: #f4f4f4;
    --ink-soft: #e2e2e2;
    --rule: #e8e8e8;
  }
  * { margin: 0; padding: 0; box-sizing: border-box; }
  html, body { width: 900px; height: 1200px; overflow: hidden; }
  body {
    background: var(--backdrop);
    font-family: "Montserrat", Arial, sans-serif;
    color: var(--ink);
    position: relative;
  }
  .card {
    position: absolute;
    left: 80px;
    width: 742px;
    height: 441px;
    background: var(--card);
    border-radius: 22px;
    box-shadow: 0 6px 18px rgba(0,0,0,0.25);
  }
  .card--front { top: 131px; }
  .card--back { top: 638px; }
  .abs { position: absolute; white-space: nowrap; }

  /* front */
  .person-name { left: 34px; top: 192px; font-size: 25px; font-weight: 700; }
  .person-title { left: 34px; top: 223px; font-size: 15px; font-weight: 400; color: var(--ink-soft); }
  .name-rule { left: 34px; top: 256px; width: 286px; height: 1.5px; background: var(--rule); }
  .brand-name {
    font-size: 27px; font-weight: 400; letter-spacing: 1.5px;
    transform: translateX(-50%);
  }
  .card--front .brand-name { left: 512px; top: 222px; }
  .contact-list { left: 34px; top: 326px; list-style: none; }
  .contact-list li { display: flex; align-items: center; height: 29.5px; font-size: 15px; font-weight: 400; }
  .contact-list svg { width: 16px; height: 16px; margin-right: 15px; fill: var(--ink); }
  .license { right: 56px; top: 382px; font-size: 15px; font-weight: 400; }

  /* back */
  .card--back .brand-name { left: 358px; top: 168px; }
  .services-title { left: 50%; transform: translateX(-50%); top: 257px; font-size: 20px; font-weight: 700; }
  .services-rule { left: 288px; top: 287px; width: 140px; height: 1.5px; background: var(--rule); }
  .service-rows { left: 0; right: 0; top: 330px; }
  .service-row { display: flex; justify-content: center; gap: 14px; height: 29.5px; font-size: 14.5px; font-weight: 400; }
  .service-row span::before { content: "•"; margin-right: 7px; }
</style>
</head>
<body>
  <section class="card card--front">
    <div class="abs person-name">Marcus Delling</div>
    <div class="abs person-title">Managing Director</div>
    <div class="abs name-rule"></div>
    <div class="abs brand-name">HARBORLINE BUILDERS</div>
    <ul class="abs contact-list">
      <li><svg viewBox="0 0 16 16" aria-hidden="true"><path d="M2 6c0-2 2-3 6-3s6 1 6 3v1h-3V5.5H5V7H2z"/><path d="M4 8h8l1 6H3z"/><circle cx="8" cy="11" r="1.6" fill="#232323"/></svg>858-471-6093</li>
      <li><svg viewBox="0 0 16 16" aria-hidden="true"><path d="M1 3h14v1.5L8 9 1 4.5z"/><path d="M1 6.3l7 4.4 7-4.4V13H1z"/></svg>info@brightoakbuilders.com</li>
      <li><svg viewBox="0 0 16 16" aria-hidden="true"><circle cx="8" cy="8" r="7"/><path d="M4 4c2 0 3 1 2.5 2.5S4 8 5 10s1 3 0 4M10 2c-1 2 1 3 2.5 3S14 7 13 9s-2 2-2 4" stroke="#232323" stroke-width="1.4" fill="none"/></svg>www.brightoakbuilders.com</li>
    </ul>
    <div class="abs license">CSLB Licensed No. #1048265</div>
  </section>

  <section class="card card--back">
    <div class="abs brand-name">HARBORLINE BUILDERS</div>
    <div class="abs services-title">Our Services</div>
    <div class="abs services-rule"></div>
    <div class="abs service-rows">
      <div class="service-row"><span>Remodel: Kitchen &amp; Bath</span><span>Painting: Interior &amp; Exterior</span><span>Flooring: Carpet, Vinyl, Wood</span></div>
      <div class="service-row"><span>Window: Door Replacement</span><span>Plumbing: Repair &amp; Upgrades</span><span>Energy Efficient Upgrades</span></div>
      <div class="service-row"><span>Deck &amp; Patio Construction</span><span>Water &amp; Mold Damage</span><span>Garage Renovation</span></div>
    </div>
  </section>
</body>
</html>
```